Bespoke Builders Business Card Design

We need a business card for an established builder of high quality bespoke homes in Auckland and Northland. We build and renovate homes collaboratively facilitating effective communication between owners, builders, architects, suppliers and tradespeople. We have never built or renovated a home that leaks or has faults. We only use reliable materials. We have never been sued or had legal action taken against us. We are honest builders of bespoke homes not group mass produced homes. Our niche market is in character homes. We practice sustainability and have built a lot of coastal property. We have been in business for over thirty years . We would like to see natural colors of the environment sand,sea and maybe vegetation . The design should communicate quality, sustainability,fair pricing, open communication and the originality of bespoke building. And the fact that the builder is registered.

Industry/Entity Type

Business

Contact Information for Business Card

Rowan Tellick Builders
Ph. 021583917
18 Kestrel Rd Harwood Bay Auckland 0814
PO Box 927 Mangawhai 0583

```html
<!DOCTYPE html>
<html lang="en">
<head>
<meta charset="utf-8">
<title>Rowan Tellick Builders – Business Card</title>
<link rel="stylesheet" href="https://fonts.googleapis.com/css2?family=Questrial&display=swap">
<style>
  :root {
    --page-bg: #e9e7e4;
    --card-dark: #2e2e30;
    --card-dark-edge: #1f1f21;
    --card-light: #ffffff;
    --sand-orange: #c2732f;
    --sand-orange-deep: #a85d22;
    --sea-grey: #8d99ab;
    --sea-grey-light: #b6c0cd;
    --text-grey: #7f8a9c;
  }
  * { box-sizing: border-box; margin: 0; padding: 0; }
  html, body {
    width: 1200px;
    height: 900px;
    overflow: hidden;
    background: var(--page-bg);
    font-family: "Questrial", "Century Gothic", sans-serif;
  }
  .canvas {
    position: relative;
    width: 1200px;
    height: 900px;
  }
  .card {
    position: absolute;
    left: 250px;
    width: 700px;
    height: 400px;
    border-radius: 26px;
    overflow: hidden;
    box-shadow: 0 10px 28px rgba(0,0,0,0.18);
  }
  .card--front {
    top: 30px;
    background: linear-gradient(160deg, #38383a 0%, var(--card-dark) 55%, var(--card-dark-edge) 100%);
  }
  .card--back {
    top: 470px;
    background: var(--card-light);
  }
  .brand {
    position: absolute;
    display: flex;
    align-items: center;
    gap: 14px;
    color: var(--sand-orange);
    font-weight: 400;
    white-space: nowrap;
  }
  .brand__mark {
    width: 18px;
    height: 18px;
    border-radius: 50%;
    background: var(--sand-orange);
    flex: none;
  }
  .card--front .brand {
    left: 0;
    right: 0;
    top: 170px;
    justify-content: center;
    font-size: 44px;
  }
  .card--back .brand {
    right: 48px;
    top: 52px;
    font-size: 34px;
  }
  .card--back .brand__mark { width: 14px; height: 14px; }
  .waves {
    position: absolute;
    left: 0;
    top: 0;
    width: 700px;
    height: 400px;
  }
  .contact {
    position: absolute;
    left: 56px;
    top: 190px;
    list-style: none;
    color: var(--text-grey);
    font-size: 22px;
    line-height: 34px;
  }
  .contact__item {
    display: flex;
    align-items: center;
    gap: 14px;
  }
  .contact__icon {
    width: 18px;
    height: 18px;
    flex: none;
    fill: var(--sand-orange);
  }
</style>
</head>
<body>
<main class="canvas">

  <section class="card card--front" aria-label="Card front">
    <div class="brand">
      <span class="brand__mark"></span>
      <span class="brand__name">Rowan Tellick Builders</span>
    </div>
  </section>

  <section class="card card--back" aria-label="Card back">
    <svg class="waves" viewBox="0 0 700 400" aria-hidden="true">
      <defs>
        <linearGradient id="sand-band" x1="0" y1="0" x2="1" y2="0">
          <stop offset="0" stop-color="var(--sand-orange-deep)"/>
          <stop offset="0.5" stop-color="var(--sand-orange)"/>
          <stop offset="1" stop-color="var(--sand-orange-deep)"/>
        </linearGradient>
        <linearGradient id="sea-band" x1="0" y1="0" x2="1" y2="0">
          <stop offset="0" stop-color="var(--sea-grey-light)" stop-opacity="0.2"/>
          <stop offset="0.5" stop-color="var(--sea-grey)"/>
          <stop offset="1" stop-color="var(--sea-grey-light)"/>
        </linearGradient>
      </defs>
      <path d="M250,346 C420,340 560,276 700,209 L700,294 C600,316 470,340 250,346 Z" fill="url(#sea-band)"/>
      <path d="M0,316 C140,330 300,376 450,364 C560,354 640,322 700,312 L700,400 L0,400 Z" fill="url(#sand-band)"/>
    </svg>

    <div class="brand">
      <span class="brand__mark"></span>
      <span class="brand__name">Rowan Tellick Builders</span>
    </div>

    <ul class="contact">
      <li class="contact__item">
        <svg class="contact__icon" viewBox="0 0 24 24" aria-hidden="true"><path d="M3 8c0-2 4-4 9-4s9 2 9 4v2h-5V8h-8v2H3zM6 11h12l2 8H4z"/></svg>
        <span>021583917</span>
      </li>
      <li class="contact__item">
        <svg class="contact__icon" viewBox="0 0 24 24" aria-hidden="true"><path d="M12 2a7 7 0 0 0-7 7c0 5 7 13 7 13s7-8 7-13a7 7 0 0 0-7-7zm0 9.5A2.5 2.5 0 1 1 12 6.5a2.5 2.5 0 0 1 0 5z"/></svg>
        <span>18 Kestrel Rd Harwood Bay Auckland 0814</span>
      </li>
      <li class="contact__item">
        <svg class="contact__icon" viewBox="0 0 24 24" aria-hidden="true"><path d="M12 2a7 7 0 0 0-7 7c0 5 7 13 7 13s7-8 7-13a7 7 0 0 0-7-7zm0 9.5A2.5 2.5 0 1 1 12 6.5a2.5 2.5 0 0 1 0 5z"/></svg>
        <span>PO Box 927 Mangawhai 0583</span>
      </li>
    </ul>
  </section>

</main>
</body>
</html>
```